We want to design total new business card and logo for Kestrel Building Services Ltd

Our company name Kestrel Building Services Ltd. Design new logo and business card , need hi-end luxury style art for architecture and construction industry. The card should simple but stylish. Our business focus on CONNECT tradesman to construction company, help marketing construction company tender oversea projects, managing franchise in construction sector, delivery amazing services to our client, so Logo should show the CONNECTION IDEA, CONNECTING PEOPLE, LUXURY. Visit our website for more information: kestrelgroup.example.nz

Target Market(s)

Directors or managers

Industry/Entity Type

Construction Company

Contact Information for Business Card

Name, Title, Mobile, Email, Website

Font styles to use
Serif

Colors

Designer to choose colors to be used in the design.

Requirements
Must have
• Simple and luxury, connection icon
Nice to have
• Special materials, plastic card, look through,...
• Look new ideas.

```html
<!DOCTYPE html>
<html lang="en">
<head>
<meta charset="utf-8">
<title>Kestrel Building Services Ltd – Business Card</title>
<link rel="stylesheet" href="https://fonts.googleapis.com/css2?family=PT+Serif:wght@400;700&display=swap">
<style>
  :root {
    --backdrop: #d9dcdf;
    --card-frost: #eef0f1;
    --card-edge: #c9cdd1;
    --navy: #1d4a9c;
    --deep-blue: #1f4aa0;
    --sky-blue: #2a9cc8;
    --sky-light: #6cc3e2;
    --ink: #3b3d40;
    --ink-soft: #55585c;
  }
  * { box-sizing: border-box; margin: 0; padding: 0; }
  html, body {
    width: 1200px;
    height: 971px;
    overflow: hidden;
    background: var(--backdrop);
    font-family: "PT Serif", serif;
  }
  .card {
    position: absolute;
    left: 100px;
    top: 185px;
    width: 1000px;
    height: 600px;
    border-radius: 34px;
    background: linear-gradient(135deg, #f4f5f6 0%, var(--card-frost) 55%, #e6eaed 100%);
    border: 2px solid var(--card-edge);
    overflow: hidden;
  }
  .brand {
    position: absolute;
    left: 96px;
    top: 150px;
    display: flex;
    align-items: center;
    gap: 16px;
  }
  .brand-dot {
    width: 22px;
    height: 22px;
    background: var(--navy);
  }
  .brand-name {
    font-size: 33px;
    font-weight: 700;
    color: var(--navy);
    letter-spacing: 0.3px;
  }
  .holder {
    position: absolute;
    right: 96px;
    top: 250px;
    text-align: right;
  }
  .holder-name {
    font-size: 38px;
    font-weight: 700;
    color: var(--navy);
    line-height: 1.1;
  }
  .holder-title {
    font-size: 26px;
    color: var(--ink-soft);
    margin-top: 6px;
  }
  .address {
    position: absolute;
    left: 96px;
    top: 328px;
    font-size: 25px;
    line-height: 1.35;
    color: var(--ink);
  }
  .contacts {
    position: absolute;
    left: 96px;
    top: 410px;
    list-style: none;
    font-size: 25px;
    color: var(--ink);
    line-height: 1.35;
  }
  .contacts li {
    display: flex;
    align-items: center;
    gap: 12px;
  }
  .contacts svg {
    width: 21px;
    height: 21px;
    flex: none;
  }
  .base-bands {
    position: absolute;
    left: 0;
    bottom: 0;
    width: 1000px;
    height: 72px;
  }
</style>
</head>
<body>
  <div class="card">
    <div class="brand">
      <span class="brand-dot"></span>
      <span class="brand-name">Kestrel Building Services Ltd</span>
    </div>

    <div class="holder">
      <p class="holder-name">Daniel Hartley</p>
      <p class="holder-title">Managing Director</p>
    </div>

    <p class="address">18 Harbour Lane, Westmere<br>Auckland 1022, New Zealand</p>

    <ul class="contacts">
      <li>
        <svg viewBox="0 0 24 24" aria-hidden="true"><path fill="var(--navy)" d="M6.6 10.8a15.1 15.1 0 0 0 6.6 6.6l2.2-2.2c.3-.3.7-.4 1-.2 1.1.4 2.3.6 3.6.6.6 0 1 .4 1 1V20c0 .6-.4 1-1 1A17 17 0 0 1 3 4c0-.6.4-1 1-1h3.5c.6 0 1 .4 1 1 0 1.3.2 2.5.6 3.6.1.3 0 .7-.2 1z"/></svg>
        <span>0800 555 217</span>
      </li>
      <li>
        <svg viewBox="0 0 24 24" aria-hidden="true"><rect x="2.5" y="5" width="19" height="14" fill="none" stroke="var(--navy)" stroke-width="2"/><path d="M2.5 5l9.5 8 9.5-8M2.5 19l7-6.5M21.5 19l-7-6.5" fill="none" stroke="var(--navy)" stroke-width="2"/></svg>
        <span>daniel@kestrelgroup.example.nz</span>
      </li>
      <li>
        <svg viewBox="0 0 24 24" aria-hidden="true"><g fill="none" stroke="var(--sky-blue)" stroke-width="1.8"><circle cx="12" cy="12" r="9.5"/><ellipse cx="12" cy="12" rx="4.2" ry="9.5"/><path d="M2.5 12h19M4 7h16M4 17h16"/></g></svg>
        <span>www.kestrelgroup.example.nz</span>
      </li>
    </ul>

    <svg class="base-bands" viewBox="0 0 1000 72" preserveAspectRatio="none" aria-hidden="true">
      <defs>
        <linearGradient id="sky-band" x1="0" y1="0" x2="1" y2="0">
          <stop offset="0" stop-color="var(--sky-light)"/>
          <stop offset="1" stop-color="var(--sky-blue)"/>
        </linearGradient>
      </defs>
      <polygon points="0,22 420,22 404,72 0,72" fill="var(--deep-blue)"/>
      <polygon points="430,22 412,72 1000,72 1000,0" fill="url(#sky-band)"/>
    </svg>
  </div>
</body>
</html>
```